We are a recruitment company based in Norwich/Cambridge England.
I have included our company logo which we want to remain the same.

What we are looking for is a new creative Business card which will really stand out!!

Contact Information for Business Card

Harriet Dunmore
email: Harriet@plavex.co.uk
Address: Brackwell House
Fenmoor Enterprise Park
Partridge Way
Norwich
QB9 3KX
Tel:01632 960418

```html
<!DOCTYPE html>
<html lang="en">
<head>
<meta charset="utf-8">
<title>Plavex Business Card</title>
<link rel="stylesheet" href="https://fonts.googleapis.com/css2?family=Oswald:wght@500&family=Roboto:wght@400;500&display=swap">
<style>
  :root {
    --backdrop: #3a3a3a;
    --card: #262626;
    --accent: #8dc63f;
    --text: #f2f2f2;
    --muted: #9a9a9a;
    --divider: #6a6a6a;
  }
  * { margin: 0; padding: 0; box-sizing: border-box; }
  html, body { width: 1200px; height: 900px; overflow: hidden; }
  body {
    background: var(--backdrop);
    font-family: "Roboto", Arial, sans-serif;
    color: var(--text);
    position: relative;
  }
  .card {
    position: absolute;
    left: 250px;
    width: 700px;
    height: 380px;
    background: var(--card);
    border-radius: 3px;
    box-shadow: 0 6px 18px rgba(0,0,0,0.35);
  }
  .card-front { top: 50px; }
  .card-back { top: 470px; }

  .brand {
    position: absolute;
    top: 115px;
    left: 0;
    width: 100%;
    display: flex;
    justify-content: center;
    align-items: center;
    gap: 16px;
  }
  .brand-dot {
    width: 54px; height: 54px;
    border-radius: 50%;
    background: var(--accent);
  }
  .brand-name {
    font-family: "Roboto", Arial, sans-serif;
    font-weight: 500;
    font-size: 56px;
    color: var(--accent);
    letter-spacing: 0.5px;
  }
  .front-web {
    position: absolute;
    top: 252px;
    width: 100%;
    text-align: center;
    font-size: 17px;
    letter-spacing: 9px;
    color: var(--text);
  }

  .identity {
    position: absolute;
    top: 140px;
    right: 400px;
    text-align: right;
  }
  .person-name {
    font-family: "Oswald", "Arial Narrow", sans-serif;
    font-weight: 500;
    font-size: 34px;
    color: var(--accent);
    line-height: 1.1;
    text-transform: uppercase;
  }
  .person-role {
    font-size: 17px;
    font-weight: 500;
    color: var(--muted);
    text-transform: uppercase;
    margin-top: 2px;
  }
  .divider {
    position: absolute;
    left: 320px;
    top: 95px;
    width: 1px;
    height: 170px;
    background: linear-gradient(to bottom, transparent, var(--divider) 20%, var(--divider) 80%, transparent);
  }
  .contact-list {
    position: absolute;
    left: 345px;
    top: 112px;
    list-style: none;
  }
  .contact-item {
    display: flex;
    align-items: center;
    gap: 10px;
    font-size: 17px;
    height: 27px;
  }
  .contact-item svg { width: 16px; height: 16px; fill: var(--accent); flex: none; }
  .address {
    position: absolute;
    left: 60px;
    top: 305px;
    display: flex;
    align-items: center;
    gap: 8px;
    font-size: 18px;
  }
  .address svg { width: 16px; height: 20px; fill: var(--accent); }
</style>
</head>
<body>
  <section class="card card-front">
    <div class="brand">
      <span class="brand-dot"></span>
      <span class="brand-name">Plavex</span>
    </div>
    <p class="front-web">www.plavex.co.uk</p>
  </section>

  <section class="card card-back">
    <div class="identity">
      <h1 class="person-name">Harriet Dunmore</h1>
      <p class="person-role">CEO/Founder</p>
    </div>
    <div class="divider"></div>
    <ul class="contact-list">
      <li class="contact-item">
        <svg viewBox="0 0 16 16" aria-hidden="true"><path d="M3.5 1 6 3.8 4.7 5.6c.9 2.2 3.5 4.8 5.7 5.7l1.8-1.3L15 12.5l-1.6 2.2C7.6 15 1 8.4 1.3 2.6Z"/></svg>
        <span>01632 960418</span>
      </li>
      <li class="contact-item">
        <svg viewBox="0 0 16 16" aria-hidden="true"><path d="M4 0h8a1 1 0 0 1 1 1v14a1 1 0 0 1-1 1H4a1 1 0 0 1-1-1V1a1 1 0 0 1 1-1Zm1 2v10h6V2Zm3 11a1 1 0 1 0 0 2 1 1 0 0 0 0-2Z"/></svg>
        <span>07700 900318</span>
      </li>
      <li class="contact-item">
        <svg viewBox="0 0 16 16" aria-hidden="true"><path d="M4 1h7v4H4Zm-3 5h14v7h-3v2H4v-2H1Zm5 5v3h4v-3Z"/></svg>
        <span>01632 960419</span>
      </li>
      <li class="contact-item">
        <svg viewBox="0 0 16 16" aria-hidden="true"><path d="M1 3h14v1.2L8 9 1 4.2Zm0 2.6 7 4.8 7-4.8V13H1Z"/></svg>
        <span>Harriet@plavex.co.uk</span>
      </li>
      <li class="contact-item">
        <svg viewBox="0 0 16 16" aria-hidden="true"><circle cx="8" cy="8" r="7"/></svg>
        <span>www.plavex.co.uk</span>
      </li>
    </ul>
    <p class="address">
      <svg viewBox="0 0 16 20" aria-hidden="true"><path d="M8 0a7 7 0 0 1 7 7c0 5-7 13-7 13S1 12 1 7a7 7 0 0 1 7-7Zm0 4a3 3 0 1 0 0 6 3 3 0 0 0 0-6Z"/></svg>
      <span>Brackwell House, Fenmoor Enterprise Park, Partridge Way, Norwich QB9 3KX</span>
    </p>
  </section>
</body>
</html>
```